Beacon Advisory Website

I currently have a website www.beaconadvisoryinc.com. We are a IT Consulting Company. Our website will pretty much tell out our services. I am looking to enhance my website and make it look more professional. Looking for very classy and Contemporary look and design for my website.

It Company

```html
<!DOCTYPE html>
<html lang="en">
<head>
<meta charset="utf-8">
<title>Beacon Advisory</title>
<link href="https://fonts.googleapis.com/css2?family=Open+Sans:wght@400;600;700&family=Roboto+Condensed:wght@400;700&display=swap" rel="stylesheet">
<style>
:root{
  --blue:#0a86c4;
  --blue-dark:#0a6ea3;
  --ink:#4a4a4a;
  --muted:#6b6b6b;
  --grey-band:#e1e1e1;
  --contact-band:#f2f2f2;
  --white:#ffffff;
}
*{margin:0;padding:0;box-sizing:border-box}
html,body{width:745px;height:1200px;overflow:hidden;background:var(--white)}
body{position:relative;font-family:'Open Sans',sans-serif;color:var(--ink)}
.abs{position:absolute}
.cond{font-family:'Roboto Condensed',sans-serif}

/* header */
.header{left:0;top:0;width:745px;height:80px;background:var(--white)}
.brand{left:48px;top:18px;display:flex;align-items:center;gap:8px}
.brand-mark{width:30px;height:30px;border-radius:50%;background:var(--blue)}
.brand-name{font-family:'Roboto Condensed',sans-serif;font-weight:700;font-size:20px;color:var(--blue);letter-spacing:.5px}
.nav{left:254px;top:24px;display:flex;align-items:center;font-family:'Roboto Condensed',sans-serif;font-size:12.5px;color:#444}
.nav a{text-decoration:none;color:inherit;padding:0 10.5px;height:32px;line-height:32px}
.nav a.active{border:1px solid var(--blue-dark);color:var(--blue-dark);padding:0 12px}

/* hero */
.hero{left:0;top:80px;width:745px;height:357px;background:linear-gradient(100deg,#dfe4e8 0%,#cfd5da 35%,#b9c0c6 60%,#3b4450 88%,#1e252d 100%)}

.feature{top:407px;width:194px;height:142px;background:var(--blue);color:var(--white);text-align:center}
.feature-shadow{top:549px;width:194px;height:36px;background:radial-gradient(ellipse 50% 100% at 50% 0,rgba(0,0,0,.13),rgba(0,0,0,0))}
.feature-icon{width:78px;height:78px;border-radius:50%;background:var(--white);border:3px solid var(--blue);top:-40px;left:58px;display:flex;align-items:center;justify-content:center}
.feature h3{font-family:'Roboto Condensed',sans-serif;font-weight:400;font-size:17px;margin-top:46px;letter-spacing:.2px}
.feature p{font-size:10px;line-height:15.5px;margin:6px 12px 0}

/* welcome */
.welcome-title{left:0;top:600px;width:745px;text-align:center;font-family:'Roboto Condensed',sans-serif;font-size:27px;color:#555}
.hl{color:var(--blue)}
.welcome-text{left:118px;top:641px;width:510px;text-align:center;font-size:10px;line-height:15.5px;color:var(--muted)}
.btn{left:321px;top:705px;width:103px;height:29px;border:1px solid var(--blue-dark);color:var(--blue-dark);font-family:'Roboto Condensed',sans-serif;font-size:13px;text-align:center;line-height:27px}

/* services */
.services{left:0;top:773px;width:745px;height:272px;background:var(--grey-band)}
.services-title{left:0;top:800px;width:745px;text-align:center;font-family:'Roboto Condensed',sans-serif;font-size:27px;color:#555}
.service{top:846px;width:146px;text-align:center}
.service-photo{width:146px;height:84px}
.service h4{font-family:'Roboto Condensed',sans-serif;font-weight:400;font-size:15px;color:var(--blue);margin-top:7px;white-space:nowrap}
.service p{font-size:10px;line-height:15.5px;color:var(--muted);margin-top:6px}

/* contact band */
.contact{left:0;top:1045px;width:745px;height:78px;background:var(--contact-band)}
.contact-icon{width:42px;height:42px;border-radius:50%;background:var(--white);border:1px solid #ddd;display:flex;align-items:center;justify-content:center}
.contact-text{font-size:10px;line-height:15.5px;color:#555}
.contact-text strong{font-weight:700;color:#444}

/* footer */
.footer{left:0;top:1123px;width:745px;height:77px;background:var(--blue)}
.footer-links{left:49px;top:1136px;display:flex;gap:16px;font-size:11px;color:var(--white)}
.copyright{left:49px;top:1162px;font-size:10px;color:var(--white)}
.copyright strong{font-weight:700}
.social{top:1143px;width:35px;height:35px;border-radius:50%;border:2px solid var(--white);background:var(--blue)}
.social.first{background:var(--white);border-color:#cfe3ef}
</style>
</head>
<body>

<header class="abs header">
  <div class="abs brand">
    <span class="brand-mark"></span>
    <span class="brand-name">BEACON ADVISORY</span>
  </div>
  <nav class="abs nav">
    <a class="active">HOME</a><a>ABOUT</a><a>SERVICES</a><a>SOLUTION</a><a>RESOURCES</a><a>CAREER</a><a>CONTACT</a>
  </nav>
</header>

<div class="abs hero" role="img" aria-label="Photo of business consultants talking around a meeting table"></div>

<div class="abs feature-shadow" style="left:48px"></div>
<div class="abs feature-shadow" style="left:275px"></div>
<div class="abs feature-shadow" style="left:503px"></div>

<section class="abs feature" style="left:48px">
  <div class="abs feature-icon">
    <svg width="40" height="36" viewBox="0 0 40 36" fill="#0a86c4">
      <circle cx="9" cy="5" r="3.5"/><circle cx="20" cy="4" r="3.5"/><circle cx="31" cy="5" r="3.5"/>
      <rect x="5" y="10" width="8" height="10" rx="2"/><rect x="27" y="10" width="8" height="10" rx="2"/>
      <rect x="16" y="9" width="8" height="11" rx="2"/>
      <rect x="2" y="20" width="36" height="3"/>
      <rect x="10" y="23" width="3" height="12"/><rect x="27" y="23" width="3" height="12"/>
      <rect x="18.5" y="23" width="3" height="8"/>
    </svg>
  </div>
  <h3>Dashboards</h3>
  <p>Dashboards are a key component of every organization's Performance Management and Business...</p>
</section>

<section class="abs feature" style="left:275px">
  <div class="abs feature-icon">
    <svg width="40" height="38" viewBox="0 0 40 38" fill="#0a86c4">
      <ellipse cx="17" cy="6" rx="14" ry="5"/>
      <path d="M3 10c0 3 6 5 14 5s14-2 14-5v6c0 3-6 5-14 5S3 19 3 16z"/>
      <path d="M3 20c0 3 6 5 14 5 2 0 4 0 6-.5v6c-2 .4-4 .5-6 .5-8 0-14-2-14-5z"/>
      <circle cx="31" cy="28" r="6"/>
      <circle cx="31" cy="28" r="2.3" fill="#fff"/>
      <rect x="29.5" y="19" width="3" height="4"/><rect x="29.5" y="33" width="3" height="4"/>
      <rect x="22" y="26.5" width="4" height="3"/><rect x="36" y="26.5" width="4" height="3"/>
    </svg>
  </div>
  <h3>Data Warehousing</h3>
  <p>A data warehouse is the concept of data extracted from operational systems and made available...</p>
</section>

<section class="abs feature" style="left:503px">
  <div class="abs feature-icon">
    <svg width="40" height="36" viewBox="0 0 40 36" fill="#0a86c4">
      <rect x="15" y="1" width="10" height="9" rx="1.5"/>
      <rect x="18.8" y="10" width="2.4" height="7"/>
      <rect x="6" y="16" width="28" height="2.4"/>
      <rect x="6" y="16" width="2.4" height="8"/><rect x="18.8" y="16" width="2.4" height="8"/><rect x="31.6" y="16" width="2.4" height="8"/>
      <rect x="2" y="24" width="10" height="9" rx="1.5"/><rect x="15" y="24" width="10" height="9" rx="1.5"/><rect x="28" y="24" width="10" height="9" rx="1.5"/>
    </svg>
  </div>
  <h3 style="letter-spacing:3px">BPM</h3>
  <p>Beacon Advisory having Vantra Certified Consultants in to provide Business Process Management...</p>
</section>

<h1 class="abs welcome-title">WELCOME TO <span class="hl">BEACON ADVISORY</span></h1>
<p class="abs welcome-text">Today's IT market is a dynamic, fast-paced industry, with ever-increasing demands. Meeting these demands for over 25 years, Beacon Advisory maintains a global presence, aggressively recruiting expertly qualified IT and Management Professionals from around the world.</p>
<div class="abs btn">READ MORE</div>

<div class="abs services"></div>
<h2 class="abs services-title">OUR <span class="hl">SERVICES</span></h2>

<article class="abs service" style="left:48px">
  <div class="service-photo" role="img" aria-label="Photo of a trainer presenting to a seated team" style="background:linear-gradient(135deg,#e4e8ec,#a9b3bd)"></div>
  <h4>Technology</h4>
  <p>Beacon Advisory Training programs are perfect for individuals to enhance their...</p>
</article>
<article class="abs service" style="left:216px">
  <div class="service-photo" role="img" aria-label="Photo of hands holding a tablet with glowing network graphics" style="background:linear-gradient(135deg,#1a2633,#4f7ea6 60%,#2a3b4c)"></div>
  <h4>Application Developement</h4>
  <p>Drawing on our experience in all major industries, we develop solutions that meet...</p>
</article>
<article class="abs service" style="left:384px">
  <div class="service-photo" role="img" aria-label="Photo of two businessmen reviewing documents at a desk" style="background:linear-gradient(135deg,#d9cfc2,#6e6a66 60%,#3a3836)"></div>
  <h4>Enterprise Integration</h4>
  <p>As organizations work to achieve and sustain competitive advantage...</p>
</article>
<article class="abs service" style="left:551px">
  <div class="service-photo" role="img" aria-label="Photo of colleagues shaking hands in an office" style="background:linear-gradient(135deg,#e9ecee,#9ea8b1 60%,#5d6670)"></div>
  <h4>IT Consulting</h4>
  <p>Beacon Advisory Training programs are perfect for individuals to enhance their...</p>
</article>

<div class="abs contact"></div>
<div class="abs contact-icon" style="left:70px;top:1061px">
  <svg width="14" height="18" viewBox="0 0 14 18"><path d="M7 0a7 7 0 0 1 7 7c0 5-7 11-7 11S0 12 0 7a7 7 0 0 1 7-7z" fill="#0a86c4"/><circle cx="7" cy="7" r="2.5" fill="#fff"/></svg>
</div>
<div class="abs contact-text" style="left:122px;top:1059px">
  <strong>HEAD OFFICE</strong><br>240 Harbor Lane, Suite 310<br>Millbrook, NJ 07999
</div>
<div class="abs contact-icon" style="left:384px;top:1061px">
  <svg width="18" height="18" viewBox="0 0 24 24"><path d="M6.6 10.8a15.1 15.1 0 0 0 6.6 6.6l2.2-2.2c.3-.3.7-.4 1-.2 1.1.4 2.3.6 3.6.6.6 0 1 .4 1 1V20c0 .6-.4 1-1 1A17 17 0 0 1 3 4c0-.6.4-1 1-1h3.5c.6 0 1 .4 1 1 0 1.3.2 2.5.6 3.6.1.3 0 .7-.2 1z" fill="#0a86c4"/></svg>
</div>
<div class="abs contact-text" style="left:436px;top:1059px">
  <strong>CONTACT US</strong><br>Phone No : +1 (555) 014 2280<br>Email : info@beaconadvisoryinc.com
</div>

<footer class="abs footer"></footer>
<div class="abs footer-links"><span>Home</span><span>About</span><span>Services</span><span>Solution</span><span>Resources</span><span>Career</span><span>Contact</span></div>
<div class="abs copyright">© <strong>Beacon Advisory Inc</strong> - 2016. All Rights Reserved.</div>
<div class="abs social first" style="left:561px" aria-label="Social link"></div>
<div class="abs social" style="left:612px" aria-label="Social link"></div>
<div class="abs social" style="left:661px" aria-label="Social link"></div>

</body>
</html>
```